Boutique custom software development company needs new business card

Our nearly 20 year old custom software development company would like to better include the fact that we are now providing Bitcoin services. These new services are B2B include education (how to acquire and securely hold Bitcoin) and integrating Bitcoin payments into existing ecommerce sites or other existing systems. Please keep the card clean and simple. Attached is our current design and some other files. vextorial.com

Target Market(s)

businesses owners interested in long term relationship

Industry/Entity Type

Custom software development and Bitcoin

Contact Information for Business Card

Dale Parker, dale@vextorial.com, vextorial.com, (888) 555-VXTRL

Font styles to use
Other font styles liked:
• monospace

Requirements
Must have
• double-sided
Nice to have
• clean and simple
Should not have
• physical address

```html
<!DOCTYPE html>
<html lang="en">
<head>
<meta charset="utf-8">
<title>Vextorial Business Card</title>
<link href="https://fonts.googleapis.com/css2?family=Source+Sans+3:wght@400;600;700&display=swap" rel="stylesheet">
<style>
  :root {
    --backdrop: #1e1e1e;
    --card-white: #ffffff;
    --brand-blue: #3e72b8;
    --brand-orange: #f37c22;
    --ink: #474747;
  }
  * { margin: 0; padding: 0; box-sizing: border-box; }
  html, body {
    width: 1200px; height: 1200px; overflow: hidden;
    background: var(--backdrop);
    font-family: "Source Sans 3", "Source Sans Pro", sans-serif;
  }
  .card {
    position: absolute; left: 250px; width: 700px; height: 400px;
    border-radius: 27px; overflow: hidden;
  }
  .card-front { top: 170px; background: var(--card-white); }
  .card-back { top: 631px; background: var(--brand-blue); }
  .card-shapes { position: absolute; inset: 0; }

  .wordmark {
    position: absolute; left: 60px; top: 62px;
    font-size: 52px; font-weight: 700; letter-spacing: 1px;
    color: var(--brand-blue); line-height: 1;
  }
  .tagline {
    position: absolute; left: 71px; top: 120px;
    font-size: 18px; color: var(--brand-blue); letter-spacing: -0.3px;
  }

  .contact-list { position: absolute; left: 76px; top: 264px; list-style: none; }
  .contact-item {
    display: flex; align-items: center; gap: 10px;
    height: 25px; font-size: 17px; color: var(--ink); letter-spacing: 0.5px;
  }
  .contact-icon { width: 14px; height: 14px; flex: none; }

  .name-block { position: absolute; right: 49px; top: 263px; text-align: right; color: #fff; }
  .person-name { font-size: 31px; font-weight: 700; letter-spacing: 1.5px; line-height: 1; }
  .person-title { font-size: 19px; letter-spacing: 0.5px; margin-top: 2px; }

  .service-list {
    position: absolute; right: 46px; top: 257px; list-style: none; text-align: right;
  }
  .service-item {
    display: flex; justify-content: flex-end; align-items: center; gap: 14px;
    height: 27px; font-size: 18px; color: #fff; letter-spacing: 0.4px;
  }
  .service-item::after {
    content: ""; width: 8px; height: 8px; background: #fff; flex: none;
  }
</style>
</head>
<body>

<section class="card card-front">
  <svg class="card-shapes" width="700" height="400" viewBox="0 0 700 400">
    <polygon points="0,253 49,253 0,327" fill="var(--brand-blue)"/>
    <polygon points="410,253 700,253 700,330 360,330" fill="var(--brand-orange)"/>
  </svg>

  <div class="wordmark">VEXTORIAL</div>
  <div class="tagline">developer of custom applications</div>

  <ul class="contact-list">
    <li class="contact-item">
      <svg class="contact-icon" viewBox="0 0 14 14"><path d="M3 1l2.5 2.5-1.3 1.6c.8 1.8 2.5 3.5 4.2 4.3l1.6-1.3L12.5 10.6 11 13C6 12.5 1.5 8 1 3z" fill="var(--brand-orange)"/></svg>
      (888) 555-VXTRL
    </li>
    <li class="contact-item">
      <svg class="contact-icon" viewBox="0 0 14 14"><rect x="1" y="3" width="12" height="8.5" fill="var(--brand-orange)"/><path d="M1 3l6 5 6-5" fill="none" stroke="#fff" stroke-width="1.2"/></svg>
      dale@vextorial.com
    </li>
    <li class="contact-item">
      <svg class="contact-icon" viewBox="0 0 14 14"><circle cx="7" cy="7" r="6" fill="var(--brand-orange)"/><path d="M4 4.5c1.5 0 2 1.5 1 2.5s.5 3 1.5 3.5M9 3c-.5 1.5.5 2.5 2 2.5" fill="none" stroke="#fff" stroke-width="1.1"/></svg>
      vextorial.com
    </li>
  </ul>

  <div class="name-block">
    <div class="person-name">DALE PARKER</div>
    <div class="person-title">Founding Partner</div>
  </div>
</section>

<section class="card card-back">
  <svg class="card-shapes" width="700" height="400" viewBox="0 0 700 400">
    <polygon points="0,290 48,263 133,400 0,400" fill="var(--brand-orange)"/>
  </svg>

  <ul class="service-list">
    <li class="service-item">Web &amp; Native Applications</li>
    <li class="service-item">Digital Process Automation</li>
    <li class="service-item">Cloud-Based Portals</li>
    <li class="service-item">Bitcoin Consulting</li>
  </ul>
</section>

</body>
</html>
```